Quorva - corporate Business Card

We need a good look and innovative business card for a new start up company based in Los Angeles called "Quorva". We are in a payment business, including payment card, app, and ewallet. We are expert in online payment and Card not present (CNP) transaction.
We need an innovative, modern business card.

Our logo font is Aero Matics

Target Market(s)

Startup - Bank - Online Payment - Card Manufacturing

Industry/Entity Type

Startup

Contact Information for Business Card

phone: 555 014 7396 - Address: 4172 Marlowe blvd, Dunmore Park, CA 90299

Requirements
Must have
• Message: innovative, professional, expert, high tech, trust, online payment expert, security
Nice to have
• no comment
Should not have
• no Comment

```html
<!DOCTYPE html>
<html lang="en">
<head>
<meta charset="utf-8">
<title>Quorva – Business Card</title>
<link rel="stylesheet" href="https://fonts.googleapis.com/css2?family=Saira:wght@600&family=Open+Sans:wght@400;700&display=swap">
<style>
  :root {
    --brand-red: #b8202f;
    --stage: #2b2b2d;
    --card-white: #ffffff;
    --divider-grey: #9b9b9b;
    --text-grey: #9a9a9a;
    --blush: #f4e3df;
  }
  * { margin: 0; padding: 0; box-sizing: border-box; }
  html, body { width: 1200px; height: 880px; overflow: hidden; }
  body { background: var(--stage); position: relative; font-family: "Open Sans", sans-serif; }

  .card {
    position: absolute;
    width: 620px;
    height: 354px;
    border-radius: 22px;
    overflow: hidden;
  }

  /* Front */
  .card-front { left: 110px; top: 50px; background: var(--brand-red); }
  .front-brand {
    position: absolute; inset: 0;
    display: flex; align-items: center; justify-content: center; gap: 18px;
  }
  .brand-dot { width: 98px; height: 98px; border-radius: 50%; background: var(--card-white); }
  .brand-name {
    font-family: "Saira", sans-serif; font-weight: 600;
    color: var(--card-white); font-size: 84px; line-height: 1; letter-spacing: 1px;
  }

  /* Back */
  .card-back { left: 470px; top: 476px; background: var(--card-white); }
  .blush-circle {
    position: absolute; left: 380px; top: 60px;
    width: 300px; height: 300px; border-radius: 50%; background: var(--blush);
  }
  .header-band {
    position: absolute; left: 0; top: 0; width: 100%; height: 196px;
    background: var(--brand-red);
    border-bottom: 9px solid var(--divider-grey);
  }
  .holder { position: absolute; right: 30px; top: 30px; text-align: right; color: var(--card-white); }
  .holder-name { font-weight: 700; font-size: 21px; line-height: 1.2; }
  .holder-role { font-size: 15px; line-height: 1.2; }
  .back-brand {
    position: absolute; left: 34px; top: 96px;
    font-family: "Saira", sans-serif; font-weight: 600;
    color: var(--card-white); font-size: 76px; line-height: 1; letter-spacing: 1px;
  }
  .contact { position: absolute; left: 40px; top: 224px; color: var(--text-grey); font-size: 15px; line-height: 1.35; }
  .address { margin-bottom: 12px; }
  .contact-row { display: flex; align-items: center; gap: 9px; }
  .contact-row svg { width: 17px; height: 17px; flex: none; }
</style>
</head>
<body>
  <section class="card card-front" aria-label="Card front">
    <div class="front-brand">
      <span class="brand-dot"></span>
      <span class="brand-name">quorva</span>
    </div>
  </section>

  <section class="card card-back" aria-label="Card back">
    <div class="blush-circle"></div>
    <div class="header-band">
      <div class="holder">
        <div class="holder-name">Lena Hartwell</div>
        <div class="holder-role">Managing Director</div>
      </div>
      <div class="back-brand">quorva</div>
    </div>
    <div class="contact">
      <div class="address">4172 Marlowe blvd,<br>Dunmore Park, CA 90299</div>
      <div class="contact-row">
        <svg viewBox="0 0 20 20" aria-hidden="true"><circle cx="10" cy="10" r="10" fill="#b8202f"/><path d="M6.5 5.5l2 0 .8 2.4-1.2 1a6 6 0 0 0 3 3l1-1.2 2.4.8 0 2a1.2 1.2 0 0 1-1.3 1.2A8.5 8.5 0 0 1 5.3 6.8 1.2 1.2 0 0 1 6.5 5.5z" fill="#fff"/></svg>
        <span>555 014 7396</span>
      </div>
      <div class="contact-row">
        <svg viewBox="0 0 20 20" aria-hidden="true"><circle cx="10" cy="10" r="10" fill="#b8202f"/><rect x="5" y="6.5" width="10" height="7" rx="1" fill="#fff"/><path d="M5.4 7l4.6 3.6L14.6 7" fill="none" stroke="#b8202f" stroke-width="1"/></svg>
        <span>team@quorvapay.net</span>
      </div>
    </div>
  </section>
</body>
</html>
```